Islamic App which helps to calculate, track and pay Zakat

We need an application which helps muslim people to calculate and pay Zakat - mandatory donations which muslim should pay based on his income. The application will consist of two parts (applications) - the one which is used by "payer" and another one - used by "receiver". To make a payment "payer" will scan QR-code which "receiver" will generate in his app and show to payer. "Receiver" will have option to initiate cash withdrawal once he collected required minimum for the withdrawal.
Important that "payer" side journey to make a payment should be as short as possible - imaging same as you make donation by cash - you just gave money and left, similar experience should be with app - couple-three taps to make it. For receiver side major requirement is to keep the UI/UX as simple as possible, these guys usually are not aware about online payments (roughly speaking this part of the app should be more similar to Quillotap rather than to banking/financial app)
In this Figma I tried to sketch the UX for both sides (just to explain the idea): https://www.plovix.com/file/Rt4mWq8ZpLbN2vKe7sJd3X/Plovix-basics?type=design&node-id=2741-583016&mode=design

Target Market(s)

Muslims

Industry/Entity Type

Donations

Colors
0094D4
00A9DD
6FCCEA
C7EBF8
E9F6FB
00AB8E
00BBA5
67D7C9
C6EFE9
E9F9F6

Requirements
Must have
• The application should have soul. Design should show that this application intend to help people, not just money transfer
Nice to have
• Payment should be as quick as possible, in the sketches I showed it as banknotes/coins which user need to slide-up to pay. Maybe make it similar as Vel OS dock icons?
Should not have
• The application should not look as banking/financial app or wallet app

```html
<!DOCTYPE html>
<html lang="en">
<head>
<meta charset="utf-8">
<title>Zakat App Screens</title>
<link href="https://fonts.googleapis.com/css2?family=Poppins:wght@300;400;600;700;800&family=IBM+Plex+Sans:wght@400&display=swap" rel="stylesheet">
<style>
  :root {
    --stage: #1b4569;
    --screen: #ffffff;
    --ink: #222222;
    --ink-soft: #6b6b6b;
    --accent-text: #9cc3d6;
    --button: #5065a3;
    --field-shadow: rgba(30, 40, 60, 0.12);
    --photo-sky: #9fd3ef;
    --photo-stone: #7a5336;
    --photo-dark: #4a3020;
  }
  * { box-sizing: border-box; margin: 0; padding: 0; }
  html, body { width: 1200px; height: 789px; overflow: hidden; }
  body {
    background: var(--stage);
    font-family: "Poppins", sans-serif;
    color: var(--ink);
    position: relative;
  }
  .screen {
    position: absolute;
    top: 68px;
    width: 302px;
    height: 654px;
    background: var(--screen);
    border-radius: 34px;
    overflow: hidden;
  }
  .screen--sign-in { left: 55px; }
  .screen--code { left: 449px; }
  .screen--profile { left: 843px; }

  .status-bar {
    position: absolute; top: 10px; left: 28px; right: 24px;
    display: flex; justify-content: space-between; align-items: center;
    font-size: 11px; font-weight: 600;
  }
  .status-icons { display: flex; gap: 4px; align-items: center; }

  .app-title {
    position: absolute; top: 50px; width: 100%;
    text-align: center; font-size: 31px; font-weight: 800; letter-spacing: 1px;
  }
  .screen-heading {
    position: absolute; width: 100%; text-align: center;
    font-size: 25px; font-weight: 700; white-space: nowrap;
  }
  .screen-heading .accent { color: var(--accent-text); font-weight: 400; }

  .phone-field {
    position: absolute; left: 18px; top: 205px; width: 267px; height: 51px;
    border-radius: 6px; box-shadow: 0 3px 10px var(--field-shadow);
    display: flex; align-items: center; padding-left: 22px;
    font-family: "IBM Plex Sans", sans-serif; font-size: 15px; color: #9a9a9a;
  }
  .field-hint {
    position: absolute; left: 18px; top: 273px;
    font-size: 10.5px; color: var(--ink-soft);
  }
  .primary-button {
    position: absolute; left: 12px; width: 278px; height: 54px;
    border-radius: 27px; background: var(--button); color: #fff;
    display: flex; justify-content: center; align-items: center;
    font-size: 15px; font-weight: 700;
  }
  .sms-note {
    position: absolute; top: 182px; width: 100%; text-align: center;
    font-family: "IBM Plex Sans", sans-serif; font-size: 14.8px; line-height: 25px;
    white-space: nowrap;
  }
  .sms-note .accent { color: var(--accent-text); }
  .code-dots { position: absolute; top: 253px; left: 29px; display: flex; gap: 15px; }
  .code-dot {
    width: 50px; height: 50px; border-radius: 50%;
    background: #fff; box-shadow: 0 3px 10px var(--field-shadow);
  }

  .keypad {
    position: absolute; left: 58px;
    display: grid; grid-template-columns: repeat(3, 61px); grid-auto-rows: 55px;
  }
  .key {
    display: flex; flex-direction: column; align-items: center; justify-content: center;
    font-size: 20px; font-weight: 300; line-height: 1;
  }
  .key small { font-size: 5.5px; font-weight: 600; letter-spacing: 1.5px; margin-top: 2px; height: 6px; }

  .back-button {
    position: absolute; left: 7px; top: 38px; width: 28px; height: 28px;
  }
  .place-photo {
    position: absolute; left: 7px; top: 101px; width: 290px; height: 240px;
    border-radius: 8px;
    background: linear-gradient(180deg, var(--photo-sky) 0%, var(--photo-stone) 35%, var(--photo-dark) 100%);
  }
  .recipient-name {
    position: absolute; top: 367px; width: 100%; text-align: center;
    font-size: 28px; font-weight: 700;
  }
  .recipient-bio {
    position: absolute; top: 412px; width: 100%; text-align: center;
    font-family: "IBM Plex Sans", sans-serif; font-size: 15px;
  }
  .amount {
    position: absolute; top: 475px; width: 100%; text-align: center;
    font-size: 30px; font-weight: 700;
  }
  .pay-button {
    position: absolute; left: 117px; top: 540px; width: 69px; height: 58px;
    background: var(--button); border-radius: 3px;
    display: flex; justify-content: center; align-items: center;
  }
</style>
</head>
<body>

<section class="screen screen--sign-in">
  <div class="status-bar">
    <span>9:30</span>
    <span class="status-icons">
      <svg width="14" height="9" viewBox="0 0 14 9"><rect x="0" y="6" width="2" height="3"/><rect x="4" y="4" width="2" height="5"/><rect x="8" y="2" width="2" height="7"/><rect x="12" y="0" width="2" height="9"/></svg>
      <svg width="12" height="9" viewBox="0 0 12 9"><path d="M1 3a7 7 0 0 1 10 0M3 5.2a4 4 0 0 1 6 0" fill="none" stroke="#222" stroke-width="1.4"/><circle cx="6" cy="7.6" r="1.2"/></svg>
      <svg width="20" height="9" viewBox="0 0 20 9"><rect x="0.5" y="0.5" width="17" height="8" rx="2" fill="none" stroke="#222"/><rect x="2" y="2" width="14" height="5" rx="1"/><rect x="18.5" y="3" width="1.5" height="3"/></svg>
    </span>
  </div>
  <h1 class="app-title">ZAKAT</h1>
  <h2 class="screen-heading" style="top:136px">SIGN IN TO <span class="accent">ZAKAT APP</span></h2>
  <div class="phone-field">+971 (50) 000-00-00</div>
  <p class="field-hint">Please enter your UAE phone number</p>
  <div class="primary-button" style="top:335px">NEXT</div>
  <div class="keypad" style="top:415px">
    <div class="key">1<small></small></div><div class="key">2<small>ABC</small></div><div class="key">3<small>DEF</small></div>
    <div class="key">4<small>GHI</small></div><div class="key">5<small>JKL</small></div><div class="key">6<small>MNO</small></div>
    <div class="key">7<small>PQRS</small></div><div class="key">8<small>TUV</small></div><div class="key">9<small>WXYZ</small></div>
    <div class="key">∗<small></small></div><div class="key">0<small>+</small></div><div class="key">#<small></small></div>
  </div>
</section>

<section class="screen screen--code">
  <div class="status-bar">
    <span>9:30</span>
    <span class="status-icons">
      <svg width="14" height="9" viewBox="0 0 14 9"><rect x="0" y="6" width="2" height="3"/><rect x="4" y="4" width="2" height="5"/><rect x="8" y="2" width="2" height="7"/><rect x="12" y="0" width="2" height="9"/></svg>
      <svg width="12" height="9" viewBox="0 0 12 9"><path d="M1 3a7 7 0 0 1 10 0M3 5.2a4 4 0 0 1 6 0" fill="none" stroke="#222" stroke-width="1.4"/><circle cx="6" cy="7.6" r="1.2"/></svg>
      <svg width="20" height="9" viewBox="0 0 20 9"><rect x="0.5" y="0.5" width="17" height="8" rx="2" fill="none" stroke="#222"/><rect x="2" y="2" width="14" height="5" rx="1"/><rect x="18.5" y="3" width="1.5" height="3"/></svg>
    </span>
  </div>
  <h1 class="app-title">ZAKAT</h1>
  <h2 class="screen-heading" style="top:135px">INPUT <span class="accent">CODE</span></h2>
  <p class="sms-note">We have sent an SMS with a 4 digit code<br>to phone <span class="accent">+971 50 7428316</span></p>
  <div class="code-dots">
    <span class="code-dot"></span><span class="code-dot"></span><span class="code-dot"></span><span class="code-dot"></span>
  </div>
  <div class="primary-button" style="top:334px">SIGN IN</div>
  <div class="keypad" style="top:413px">
    <div class="key">1<small></small></div><div class="key">2<small>ABC</small></div><div class="key">3<small>DEF</small></div>
    <div class="key">4<small>GHI</small></div><div class="key">5<small>JKL</small></div><div class="key">6<small>MNO</small></div>
    <div class="key">7<small>PQRS</small></div><div class="key">8<small>TUV</small></div><div class="key">9<small>WXYZ</small></div>
    <div class="key">∗<small></small></div><div class="key">0<small>+</small></div><div class="key">#<small></small></div>
  </div>
</section>

<section class="screen screen--profile">
  <div class="status-bar">
    <span>9:30</span>
    <span class="status-icons">
      <svg width="14" height="9" viewBox="0 0 14 9"><rect x="0" y="6" width="2" height="3"/><rect x="4" y="4" width="2" height="5"/><rect x="8" y="2" width="2" height="7"/><rect x="12" y="0" width="2" height="9"/></svg>
      <svg width="12" height="9" viewBox="0 0 12 9"><path d="M1 3a7 7 0 0 1 10 0M3 5.2a4 4 0 0 1 6 0" fill="none" stroke="#222" stroke-width="1.4"/><circle cx="6" cy="7.6" r="1.2"/></svg>
      <svg width="20" height="9" viewBox="0 0 20 9"><rect x="0.5" y="0.5" width="17" height="8" rx="2" fill="none" stroke="#222"/><rect x="2" y="2" width="14" height="5" rx="1"/><rect x="18.5" y="3" width="1.5" height="3"/></svg>
    </span>
  </div>
  <svg class="back-button" viewBox="0 0 28 28" aria-label="Back">
    <circle cx="14" cy="14" r="13" fill="none" stroke="#222" stroke-width="1.2"/>
    <path d="M15.5 9.5 11 14l4.5 4.5" fill="none" stroke="#222" stroke-width="1.3"/>
  </svg>
  <div class="place-photo" role="img" aria-label="Photo of a carved stone mosque gateway with two minarets under a blue sky"></div>
  <h2 class="recipient-name">KAREEM</h2>
  <p class="recipient-bio">I am from Pakistan.I have three Kids.</p>
  <p class="amount">847AED</p>
  <div class="pay-button" aria-label="Pay">
    <svg width="38" height="38" viewBox="0 0 38 38" fill="none" stroke="#fff" stroke-width="2">
      <rect x="4" y="5" width="30" height="6"/>
      <path d="M10 11v22h18V11"/>
      <text x="19" y="28" text-anchor="middle" font-family="Poppins, sans-serif" font-size="14" font-weight="700" fill="#fff" stroke="none">$</text>
    </svg>
  </div>
</section>

</body>
</html>
```